Redesign of business card for Cedar Ridge Mechanical

We are looking for a new design for our business cards for Cedar Ridge Mechanical. We are a plumbing & HVAC construction company, operating on the West Coast of Canada and USA. Logo attached.
Industry/Entity Type
Construction - Plumbing & HVAC
Contact Information for Business Card
Name, address, phone numbers, email, website address
Look and feel
Each slider illustrates characteristics of the customer's brand and the style your logo design should communicate.

```html
<!DOCTYPE html>
<html lang="en">
<head>
<meta charset="utf-8">
<title>Cedar Ridge Mechanical — Business Card</title>
<link rel="stylesheet" href="https://fonts.googleapis.com/css2?family=Montserrat:wght@400;500;700&display=swap">
<style>
  :root {
    --backdrop: #e6e4e0;
    --card-light: #ffffff;
    --card-dark: #1f1f1f;
    --ink: #1c1c1c;
    --band: #2b2b2b;
    --band-text: #ffffff;
    --mark-on-dark: #3d3d3d;
  }
  * { margin: 0; padding: 0; box-sizing: border-box; }
  html, body {
    width: 900px; height: 1200px; overflow: hidden;
    background: var(--backdrop);
    font-family: "Montserrat", sans-serif;
    color: var(--ink);
  }
  .canvas { position: relative; width: 900px; height: 1200px; }
  .card {
    position: absolute; left: 80px; width: 742px; height: 440px;
    border-radius: 22px; overflow: hidden;
  }
  .card--front { top: 131px; background: var(--card-light); }
  .card--back { top: 638px; background: var(--card-dark); }

  .brand-name {
    position: absolute; left: 110px; top: 308px; width: 225px;
    font-weight: 700; font-size: 27px; line-height: 1.2;
    text-transform: uppercase; letter-spacing: 0.5px;
    text-align: center; color: var(--ink);
    transform: translateY(-50%); top: 228px;
  }
  .divider {
    position: absolute; left: 356px; top: 155px;
    width: 2px; height: 148px; background: var(--ink);
  }
  .person { position: absolute; left: 374px; top: 150px; }
  .person__name { font-weight: 700; font-size: 25px; line-height: 1.3; }
  .person__title { font-weight: 500; font-size: 15px; margin-top: 1px; }
  .contacts { position: absolute; left: 374px; top: 224px; list-style: none; }
  .contacts li {
    display: flex; align-items: center; gap: 11px;
    font-size: 16px; font-weight: 500; height: 30px;
  }
  .contacts svg { width: 15px; height: 15px; fill: var(--ink); flex: none; }
  .address-band {
    position: absolute; left: 0; right: 0; top: 371px; height: 35px;
    background: var(--band); color: var(--band-text);
    font-size: 16px; display: flex; align-items: center; justify-content: center;
  }

  .back-name {
    position: absolute; inset: 0;
    display: flex; align-items: center; justify-content: center;
    font-weight: 700; font-size: 42px; letter-spacing: 1px;
    text-transform: uppercase; color: var(--mark-on-dark); text-align: center;
  }
</style>
</head>
<body>
<main class="canvas">
  <section class="card card--front" aria-label="Card front">
    <div class="brand-name">Cedar Ridge Mechanical</div>
    <div class="divider"></div>
    <div class="person">
      <h1 class="person__name">Daniel Brooks</h1>
      <p class="person__title">Managing Director</p>
    </div>
    <ul class="contacts">
      <li>
        <svg viewBox="0 0 24 24" aria-hidden="true"><path d="M6.6 10.8a15.1 15.1 0 0 0 6.6 6.6l2.2-2.2a1 1 0 0 1 1-.25 11.4 11.4 0 0 0 3.6.57 1 1 0 0 1 1 1V20a1 1 0 0 1-1 1A17 17 0 0 1 3 4a1 1 0 0 1 1-1h3.5a1 1 0 0 1 1 1c0 1.25.2 2.45.57 3.6a1 1 0 0 1-.25 1z"/></svg>
        555.014.2290
      </li>
      <li>
        <svg viewBox="0 0 24 24" aria-hidden="true"><path d="M2 5h20v14H2z M2 5l10 7 10-7" fill="none" stroke="#1c1c1c" stroke-width="0"/><path d="M2 6.5V19h20V6.5l-10 7z M2.5 5h19L12 11.7z"/></svg>
        info@cedarridgemechanical.com
      </li>
      <li>
        <svg viewBox="0 0 24 24" aria-hidden="true"><path d="M12 2a10 10 0 1 0 0 20 10 10 0 0 0 0-20zm6.9 6h-2.9a15.6 15.6 0 0 0-1.4-3.6A8 8 0 0 1 18.9 8zM12 4a14 14 0 0 1 1.9 4h-3.8A14 14 0 0 1 12 4zM4.3 14a8.2 8.2 0 0 1 0-4h3.4a16.5 16.5 0 0 0 0 4zm.8 2h2.9a15.6 15.6 0 0 0 1.4 3.6A8 8 0 0 1 5.1 16zM8 8H5.1a8 8 0 0 1 4.3-3.6A15.6 15.6 0 0 0 8 8zm4 12a14 14 0 0 1-1.9-4h3.8A14 14 0 0 1 12 20zm2.3-6H9.7a14.7 14.7 0 0 1 0-4h4.6a14.7 14.7 0 0 1 0 4zm.3 5.6a15.6 15.6 0 0 0 1.4-3.6h2.9a8 8 0 0 1-4.3 3.6zm1.7-5.6a16.5 16.5 0 0 0 0-4h3.4a8.2 8.2 0 0 1 0 4z"/></svg>
        www.cedarridgemechanical.com
      </li>
    </ul>
    <div class="address-band">240 Alder Creek Road Salem, OR 97301</div>
  </section>

  <section class="card card--back" aria-label="Card back">
    <div class="back-name">Cedar Ridge Mechanical</div>
  </section>
</main>
</body>
</html>
```